One of a Kind Clean Business Card

We need to design a new business card template for our company. Our company designs and produced merchandising displays. You can see a sample of what we produce on our site www.qorvanexhibits.net. I have uploaded our logo in vector format, as well as a picture of our current business cards. We want a totally different look. We want simple and clean, looking forward to seeing what people create.
Updates

I would like to update the address for Qorvan Display Group Inc. 518 E Tollmere Ln Arlington Heights, IL 60017 Would also note. No QR codes

Industry/Entity Type

Business

Contact Information for Business Card

Need a 1 sided business card designed.

Font styles to use
Serif

Requirements
Must have
• Easy to view; Clean Design
Nice to have
• Features that promote engineering and creativity
Should not have
• Too much clutter, keep it simple

```html
<!DOCTYPE html>
<html lang="en">
<head>
<meta charset="utf-8">
<title>Qorvan Display Group Inc. – Business Card</title>
<link rel="stylesheet" href="https://fonts.googleapis.com/css2?family=Source+Serif+4:wght@400;500;600&display=swap">
<style>
  :root {
    --backdrop: #2a2a2a;
    --card: #ffffff;
    --ink: #2b2b2b;
    --ink-soft: #3a3a3a;
    --brand-red: #9b1c1f;
  }
  * { margin: 0; padding: 0; box-sizing: border-box; }
  html, body {
    width: 1200px;
    height: 1000px;
    overflow: hidden;
    background: var(--backdrop);
    font-family: "Source Serif 4", Georgia, serif;
  }
  .stage {
    width: 1200px;
    height: 1000px;
    display: flex;
    align-items: center;
    justify-content: center;
  }
  .business-card {
    position: relative;
    width: 840px;
    height: 480px;
    background: var(--card);
    border-radius: 40px;
    overflow: hidden;
  }
  .brand {
    position: absolute;
    top: 94px;
    right: 80px;
    display: flex;
    align-items: center;
    gap: 12px;
  }
  .brand-mark {
    width: 16px;
    height: 16px;
    background: var(--brand-red);
  }
  .brand-name {
    font-size: 27px;
    font-weight: 500;
    letter-spacing: 0.5px;
    color: var(--brand-red);
    white-space: nowrap;
  }
  .edge-tab {
    position: absolute;
    left: 0;
    top: 214px;
    width: 10px;
    height: 26px;
    background: var(--brand-red);
  }
  .holder-name {
    position: absolute;
    left: 68px;
    top: 204px;
    font-size: 34px;
    line-height: 44px;
    font-weight: 600;
    color: var(--ink);
    letter-spacing: 0.5px;
  }
  .address {
    position: absolute;
    left: 150px;
    top: 290px;
    font-size: 19px;
    line-height: 26px;
    color: var(--ink-soft);
    font-style: normal;
  }
  .contact-list {
    position: absolute;
    left: 210px;
    top: 350px;
    list-style: none;
  }
  .contact-item {
    display: flex;
    align-items: center;
    gap: 14px;
    height: 24px;
    font-size: 19px;
    color: var(--ink-soft);
  }
  .contact-icon {
    width: 18px;
    height: 18px;
    flex: none;
    fill: var(--brand-red);
  }
  .base-band {
    position: absolute;
    left: 0;
    bottom: 0;
    width: 100%;
    height: 22px;
    background: var(--brand-red);
  }
  .base-notch {
    position: absolute;
    left: 650px;
    bottom: 0;
    width: 6px;
    height: 22px;
    background: var(--card);
  }
</style>
</head>
<body>
<main class="stage">
  <section class="business-card" aria-label="Qorvan Display Group business card">
    <div class="brand">
      <span class="brand-mark"></span>
      <span class="brand-name">Qorvan Display Group Inc.</span>
    </div>

    <span class="edge-tab"></span>
    <h1 class="holder-name">DANA WHITCOMB</h1>

    <address class="address">
      518 E Tollmere Ln<br>
      Arlington Heights, IL 60017
    </address>

    <ul class="contact-list">
      <li class="contact-item">
        <svg class="contact-icon" viewBox="0 0 20 20" aria-hidden="true">
          <path d="M2 7c0-2 3-4 8-4s8 2 8 4v1h-4V6.5c-1-.6-2.3-.9-4-.9s-3 .3-4 .9V8H2z"/>
          <path d="M5 10l2-3h6l2 3v7H5z"/>
          <circle cx="10" cy="12.5" r="2" fill="#fff"/>
        </svg>
        <span>555-201-4830</span>
      </li>
      <li class="contact-item">
        <svg class="contact-icon" viewBox="0 0 20 20" aria-hidden="true">
          <path d="M4 2l3 0 1.5 4-2 1.5c1 2.3 2.7 4 5 5l1.5-2 4 1.5v3c0 1-1 2-2 2C8 17 3 12 2 4c0-1 1-2 2-2z"/>
        </svg>
        <span>555-318-7294</span>
      </li>
      <li class="contact-item">
        <svg class="contact-icon" viewBox="0 0 20 20" aria-hidden="true">
          <path d="M2 4h16v12H2z"/>
          <path d="M2.5 4.5L10 11l7.5-6.5" fill="none" stroke="#fff" stroke-width="1.6"/>
        </svg>
        <span>dwhitcomb@qorvanexhibits.net</span>
      </li>
      <li class="contact-item">
        <svg class="contact-icon" viewBox="0 0 20 20" aria-hidden="true">
          <circle cx="12" cy="8" r="5" fill="none" stroke="#9b1c1f" stroke-width="2.4"/>
          <path d="M8.5 11.5L3 17" stroke="#9b1c1f" stroke-width="3" stroke-linecap="round"/>
        </svg>
        <span>www.qorvanexhibits.net</span>
      </li>
    </ul>

    <div class="base-band"></div>
    <div class="base-notch"></div>
  </section>
</main>
</body>
</html>
```